Birchline Septic Solutions

Would like to see some single sided ones but would also like to see some double sided with one sided only being the logo. Owners name is Colin Vandro. Phone number is 555-214-0387
Services are pumping, inspections, installs, and repairs

Contact Information for Business Card

555-241-0387 Colin Vandro Larkford, OH

```html
<!DOCTYPE html>
<html lang="en">
<head>
<meta charset="UTF-8">
<title>Birchline Septic Solutions – Business Card</title>
<link href="https://fonts.googleapis.com/css2?family=Open+Sans:wght@400;600;700;800&display=swap" rel="stylesheet">
<style>
  :root {
    --backdrop: #222222;
    --card-white: #ffffff;
    --teal: #26bfba;
    --teal-deep: #179c97;
    --ink: #111111;
    --rule: #2a2a2a;
  }
  * { box-sizing: border-box; margin: 0; padding: 0; }
  html, body {
    width: 1200px; height: 779px; overflow: hidden;
    background: var(--backdrop);
    font-family: "Open Sans", Arial, sans-serif;
  }
  .sheet {
    position: relative; width: 1200px; height: 779px;
    display: flex; align-items: center; justify-content: center; gap: 60px;
  }
  .card {
    position: relative; width: 520px; height: 297px;
    border-radius: 22px; overflow: hidden;
  }
  .card--front { background: var(--card-white); }
  .card--back {
    background: var(--teal);
    display: flex; align-items: center; justify-content: center;
  }

  /* front: left column */
  .brand {
    position: absolute; left: 56px; top: 48px; width: 220px;
    display: flex; align-items: center; gap: 10px;
  }
  .brand__dot {
    width: 14px; height: 14px; border-radius: 50%;
    background: var(--ink); flex: none;
  }
  .brand__name {
    font-weight: 800; font-size: 21px; line-height: 1.1;
    color: var(--ink); text-transform: uppercase; letter-spacing: 0.5px;
  }
  .divider {
    position: absolute; left: 290px; top: 58px;
    width: 1.5px; height: 112px; background: var(--rule);
  }
  .services-tag {
    position: absolute; left: 190px; top: 184px;
    background: var(--teal); color: #fff;
    font-size: 12px; font-weight: 600; line-height: 1.4;
    padding: 3px 13px; border-radius: 50%;
    border: 1.5px solid var(--teal-deep);
  }
  .services {
    position: absolute; left: 30px; top: 214px;
    display: flex; gap: 10px; list-style: none;
    font-size: 15px; color: var(--ink); white-space: nowrap;
  }
  .services li { display: flex; align-items: center; gap: 5px; }
  .services li::before {
    content: ""; width: 8px; height: 8px; border-radius: 50%;
    background: var(--teal);
  }

  /* front: right column */
  .contact { position: absolute; left: 316px; top: 80px; }
  .contact__name { font-size: 27px; font-weight: 800; line-height: 1.15; color: var(--ink); white-space: nowrap; }
  .contact__first { color: var(--teal); font-weight: 600; }
  .contact__city { font-size: 15px; margin-top: 4px; padding-left: 18px; color: var(--ink); }
  .contact__phone {
    display: flex; align-items: center; gap: 5px;
    font-size: 15px; margin-top: 2px; color: var(--ink);
  }

  /* back */
  .back-brand { display: flex; align-items: center; gap: 14px; }
  .back-brand__dot {
    width: 20px; height: 20px; border-radius: 50%; background: var(--teal-deep);
  }
  .back-brand__name {
    font-weight: 800; font-size: 30px; color: var(--teal-deep);
    text-transform: uppercase; letter-spacing: 1px; line-height: 1.1;
  }
</style>
</head>
<body>
<main class="sheet">
  <section class="card card--front" aria-label="Business card front">
    <div class="brand">
      <span class="brand__dot"></span>
      <span class="brand__name">Birchline Septic Solutions</span>
    </div>
    <span class="divider"></span>
    <span class="services-tag">SERVICES</span>
    <ul class="services">
      <li>Pumping</li>
      <li>Inspections</li>
      <li>Installs</li>
      <li>And Repairs</li>
    </ul>
    <div class="contact">
      <p class="contact__name"><span class="contact__first">Colin</span> Vandro</p>
      <p class="contact__city">Larkford, OH</p>
      <p class="contact__phone">
        <svg width="13" height="13" viewBox="0 0 24 24" aria-hidden="true">
          <path fill="var(--teal)" d="M6.6 10.8a15.1 15.1 0 0 0 6.6 6.6l2.2-2.2c.3-.3.7-.4 1-.2 1.1.4 2.3.6 3.6.6.6 0 1 .4 1 1V20c0 .6-.4 1-1 1A17 17 0 0 1 3 4c0-.6.4-1 1-1h3.5c.6 0 1 .4 1 1 0 1.3.2 2.5.6 3.6.1.3 0 .7-.2 1z"/>
        </svg>
        555-241-0387
      </p>
    </div>
  </section>

  <section class="card card--back" aria-label="Business card back">
    <div class="back-brand">
      <span class="back-brand__dot"></span>
      <span class="back-brand__name">Birchline<br>Septic Solutions</span>
    </div>
  </section>
</main>
</body>
</html>
```